Flyer Design Project

We would like a double sided a5 flyer. To promote our new brand which is velmora connect, attached is the logo. This is for a mobile telecom company.
The aim of the flyer is to create brand awareness, to pormote a managed service for mobile phone connections/ tariffs. For business users and also personal use.

We would like to focus to be on offshore billing and discrete billing for users based abroad. eg students

Theme should be based around Pebblefon and Zuvaphones , one side should focus on business users and the other should focus on personal use. The focus on business users should be based around , Virtual landline numbers, where users can have a landline number connected to their mobile phones.
Should be elegant, up class ,and not to much text bullet points would be good .

Branding of telecoms QT ,K7 ,Tellurix,.
Updates

Velmora connect

Contact info for the flyer. 
info@velmoraconnect.example
www.velmoraconnect.example
0871 463 19 02 

Flyers need to look elegant and good creative designs please.

Industry/Entity Type

Telecom

```html
<!DOCTYPE html>
<html lang="en">
<head>
<meta charset="utf-8">
<title>Velmora connect – Never miss a call again</title>
<link rel="stylesheet" href="https://fonts.googleapis.com/css2?family=Archivo+Black&family=Montserrat:wght@400;600;800&family=Didact+Gothic&display=swap">
<style>
  :root {
    --navy: #16195a;
    --navy-deep: #0e1046;
    --sky: #3f8fe0;
    --sky-deep: #1d5fb8;
    --orange: #f29422;
    --orange-deep: #e2781a;
    --paper: #ffffff;
    --curl-light: #f4f4f4;
    --curl-mid: #cfcfcf;
    --curl-dark: #8e8e8e;
    --band-top: #c9c9c9;
    --band-bottom: #a9a9a9;
    --ink-dark: #1f1f1f;
    --brand-teal: #1f9c9a;
    --photo-tone: #6f8752;
  }
  html, body {
    margin: 0;
    padding: 0;
    width: 1200px;
    height: 838px;
    overflow: hidden;
    background: var(--navy);
  }
  .flyer {
    position: relative;
    width: 1200px;
    height: 838px;
    overflow: hidden;
    background: linear-gradient(180deg, var(--navy) 0%, var(--navy-deep) 100%);
    font-family: "Montserrat", Arial, sans-serif;
  }
  .flyer__shapes {
    position: absolute;
    inset: 0;
  }
  .headline {
    position: absolute;
    left: 100px;
    top: 26px;
    margin: 0;
    font-family: "Archivo Black", "Arial Black", sans-serif;
    font-weight: 400;
    font-size: 88px;
    line-height: 90px;
    letter-spacing: -1px;
    color: var(--sky);
    background: linear-gradient(180deg, #6cb2f2 0%, var(--sky) 45%, var(--sky-deep) 100%);
    -webkit-background-clip: text;
    background-clip: text;
    -webkit-text-fill-color: transparent;
    filter: drop-shadow(4px 5px 3px rgba(0, 0, 0, 0.28));
  }
  .subline {
    position: absolute;
    left: 120px;
    top: 218px;
    margin: 0;
    font-weight: 800;
    font-size: 21px;
    color: var(--navy);
  }
  .billing-tag {
    position: absolute;
    right: 38px;
    top: 22px;
    margin: 0;
    text-align: right;
    font-weight: 800;
    font-size: 25px;
    line-height: 31px;
    color: var(--paper);
  }
  .billing-tag__soft {
    font-weight: 400;
  }
  .crowd-photo {
    position: absolute;
    left: 0;
    top: 330px;
    width: 680px;
    height: 335px;
    background: linear-gradient(90deg, var(--photo-tone) 0%, var(--photo-tone) 72%, var(--navy) 100%);
  }
  .saving {
    position: absolute;
    left: 744px;
    top: 352px;
    margin: 0;
    font-family: "Didact Gothic", "Century Gothic", sans-serif;
    font-size: 46px;
    line-height: 60px;
    color: var(--paper);
  }
  .footer-band {
    position: absolute;
    left: 0;
    bottom: 0;
    width: 1200px;
    height: 173px;
    background: linear-gradient(180deg, var(--band-top) 0%, var(--band-bottom) 100%);
  }
  .brand {
    position: absolute;
    left: 58px;
    top: 30px;
    display: flex;
    align-items: center;
    gap: 22px;
  }
  .brand__mark {
    width: 90px;
    height: 90px;
    background: var(--ink-dark);
  }
  .brand__name {
    margin: 0;
    font-weight: 400;
    font-size: 42px;
    line-height: 46px;
    text-transform: uppercase;
    color: var(--ink-dark);
  }
  .brand__web {
    position: absolute;
    left: 530px;
    top: 108px;
    margin: 0;
    font-weight: 600;
    font-size: 18px;
    color: var(--ink-dark);
  }
  .networks {
    position: absolute;
    right: 30px;
    top: 52px;
    display: flex;
    align-items: center;
    gap: 28px;
    margin: 0;
    padding: 0;
    list-style: none;
  }
  .networks__item {
    font-weight: 800;
    font-size: 44px;
    color: var(--brand-teal);
  }
  .networks__item--small {
    font-size: 32px;
  }
</style>
</head>
<body>
<main class="flyer">
  <svg class="flyer__shapes" width="1200" height="838" viewBox="0 0 1200 838" aria-hidden="true">
    <defs>
      <linearGradient id="curlShade" x1="0" y1="0" x2="1" y2="1">
        <stop offset="0" stop-color="var(--curl-light)"/>
        <stop offset="0.6" stop-color="var(--curl-mid)"/>
        <stop offset="1" stop-color="var(--curl-dark)"/>
      </linearGradient>
      <linearGradient id="tagFill" x1="0" y1="0" x2="0" y2="1">
        <stop offset="0" stop-color="var(--orange)"/>
        <stop offset="1" stop-color="var(--orange-deep)"/>
      </linearGradient>
    </defs>
    <path class="header-paper" d="M0 0 H800 C870 60 950 120 1040 170 C1090 192 1140 220 1168 266 C1100 222 1000 218 880 240 C700 274 450 284 250 278 C150 274 60 262 0 252 Z" fill="var(--paper)"/>
    <path class="corner-tag" d="M800 0 H1200 V190 C1170 152 1125 132 1090 125 C1000 92 900 42 800 0 Z" fill="url(#tagFill)"/>
    <path class="page-curl" d="M800 0 C900 42 1000 92 1090 125 C1125 132 1170 152 1200 190 V200 C1186 232 1176 254 1170 268 C1148 222 1100 192 1040 170 C950 120 870 60 800 0 Z" fill="url(#curlShade)"/>
  </svg>

  <h1 class="headline">Never miss<br>a call again!</h1>
  <p class="subline">Get your landline number on your mobile.</p>

  <p class="billing-tag">Offshore <span class="billing-tag__soft">and</span><br>Discrete<br>Billing</p>

  <div class="crowd-photo" role="img" aria-label="Photo of a group of smiling young people sitting on grass, holding up their mobile phones"></div>

  <p class="saving">We will save you<br>money of your<br>existing mobile<br>provider.</p>

  <footer class="footer-band">
    <div class="brand">
      <div class="brand__mark"></div>
      <p class="brand__name">Velmora<br>Connect</p>
    </div>
    <p class="brand__web">www.velmoraconnect.example</p>
    <ul class="networks">
      <li class="networks__item">QT</li>
      <li class="networks__item">K7</li>
      <li class="networks__item networks__item--small">Tellurix</li>
    </ul>
  </footer>
</main>
</body>
</html>
```